Tiskoro

We need a business card for our company is a holding for different business all are different we try to have some air of relax and fun in our projects we add pictures of the office to give you an idea od the mood of the business

Business

```html
<!DOCTYPE html>
<html lang="en">
<head>
<meta charset="utf-8">
<title>Tiskoro – Business Card</title>
<link href="https://fonts.googleapis.com/css2?family=Alegreya+SC:wght@700;800&family=Alegreya:wght@700&display=swap" rel="stylesheet">
<style>
  :root {
    --backdrop: #2b2b2b;
    --card-white: #ffffff;
    --banana-yellow: #f2ed36;
    --cocoa-brown: #7a4a1a;
    --text-white: #ffffff;
  }
  html, body {
    margin: 0;
    padding: 0;
    width: 1200px;
    height: 1000px;
    overflow: hidden;
    background: var(--backdrop);
  }
  .canvas {
    position: relative;
    width: 1200px;
    height: 1000px;
  }
  .card {
    position: absolute;
    width: 700px;
    height: 400px;
    background: var(--card-white);
    display: flex;
    box-sizing: border-box;
  }
  .card--front { left: 440px; top: 300px; }
  .card--back {
    left: -120px;
    top: 300px;
    transform: rotate(-90deg) scale(0.86);
    transform-origin: center;
  }
  .brand-panel {
    width: 380px;
    height: 100%;
    padding: 22px 18px 22px 22px;
    box-sizing: border-box;
  }
  .brand-field {
    width: 100%;
    height: 100%;
    background: var(--card-white);
    border: 3px solid var(--banana-yellow);
    box-sizing: border-box;
    display: flex;
    align-items: center;
    justify-content: center;
    gap: 18px;
  }
  .brand-mark {
    width: 34px;
    height: 34px;
    background: var(--banana-yellow);
  }
  .brand-name {
    font-family: "Alegreya SC", Georgia, serif;
    font-weight: 800;
    font-size: 62px;
    color: var(--cocoa-brown);
    line-height: 1;
  }
  .info-panel {
    flex: 1;
    background: var(--banana-yellow);
    position: relative;
    color: var(--text-white);
    text-align: right;
  }
  .person {
    position: absolute;
    right: 28px;
    top: 100px;
  }
  .person__name {
    font-family: "Alegreya SC", Georgia, serif;
    font-weight: 700;
    font-size: 30px;
    line-height: 1;
    white-space: nowrap;
  }
  .person__role {
    font-family: "Alegreya", Georgia, serif;
    font-weight: 700;
    font-size: 21px;
    line-height: 1.1;
  }
  .contacts {
    position: absolute;
    right: 28px;
    top: 250px;
    font-family: "Alegreya", Georgia, serif;
    font-weight: 700;
    font-size: 25px;
    line-height: 1.35;
    letter-spacing: 1px;
    font-variant-numeric: lining-nums;
    white-space: nowrap;
  }
  .contacts__email { font-size: 21px; letter-spacing: 0.5px; }
</style>
</head>
<body>
<main class="canvas">
  <section class="card card--back" aria-label="Tiskoro business card, portrait side">
    <div class="brand-panel">
      <div class="brand-field">
        <span class="brand-mark"></span>
        <span class="brand-name">Tiskoro</span>
      </div>
    </div>
    <div class="info-panel">
      <div class="person">
        <div class="person__name">Name Surname</div>
        <div class="person__role">Position</div>
      </div>
      <div class="contacts">
        <div>031 48 617</div>
        <div>052 73 905</div>
        <div class="contacts__email">hello@tiskoro.com</div>
      </div>
    </div>
  </section>

  <section class="card card--front" aria-label="Tiskoro business card, landscape side">
    <div class="brand-panel">
      <div class="brand-field">
        <span class="brand-mark"></span>
        <span class="brand-name">Tiskoro</span>
      </div>
    </div>
    <div class="info-panel">
      <div class="person">
        <div class="person__name">Name Surname</div>
        <div class="person__role">Position</div>
      </div>
      <div class="contacts">
        <div>031 48 617</div>
        <div>052 73 905</div>
        <div class="contacts__email">hello@tiskoro.com</div>
      </div>
    </div>
  </section>
</main>
</body>
</html>
```